Ward Compass Business Card Design*

We need a business card design for our company Ward Compass. Our company is specialized in providing online consulting services regarding medical institutions, hospitals and doctors. We work with patients worldwide looking to choose between healthcare providers. We have a website you may use as a reference, where we list doctors and clinics worldwide. So we target Medical providers as well as patients worldwide.
Target Market(s)
Medical Providers and patients around the world
Industry/Entity Type
Medical
Contact Information for Business Card
Salwa Kettani
CEO
+90 612 348 2175
info@wardcompass.example
www.wardcompass.example
14 Annakhil 7 H.R.B. Rabat, Morocco
Requirements
Must have
- Company logo/name on one full side, personal info and smaller logo and company name on the other side.
Nice to have
- Smart and elegant design

```html
<!DOCTYPE html>
<html lang="en">
<head>
<meta charset="utf-8">
<title>Ward Compass – Business Card</title>
<link rel="stylesheet" href="https://fonts.googleapis.com/css2?family=Montserrat:wght@300;400;500&display=swap">
<style>
  :root {
    --backdrop: #151617;
    --card: #2a2b2d;
    --ink-grey: #9a9da1;
    --ink-soft: #7d8084;
    --brand-blue: #1f4f8f;
    --accent-blue: #2d5ea8;
  }
  * { margin: 0; padding: 0; box-sizing: border-box; }
  html, body {
    width: 1200px; height: 900px; overflow: hidden;
    background: var(--backdrop);
    font-family: "Montserrat", sans-serif;
  }
  .stage {
    position: relative; width: 1200px; height: 900px;
  }
  .card {
    position: absolute; top: 300px;
    width: 520px; height: 300px;
    background: var(--card);
    overflow: hidden;
    box-shadow: 0 18px 40px rgba(0,0,0,.45);
  }
  .card--back { left: 60px; }
  .card--front { left: 620px; }

  /* Shared brand lockup */
  .brand {
    display: flex; align-items: center; gap: 12px;
  }
  .brand__dot {
    border-radius: 50%; background: var(--brand-blue); flex: none;
  }
  .brand__name {
    font-weight: 400; letter-spacing: .08em; text-transform: uppercase;
    color: var(--ink-grey);
  }

  /* Front side */
  .card--front .brand {
    position: absolute; left: 50%; top: 50%;
    transform: translate(-50%, -50%);
  }
  .card--front .brand__dot { width: 34px; height: 34px; }
  .card--front .brand__name { font-size: 24px; }

  /* Back side */
  .card--back .brand { position: absolute; left: 34px; top: 32px; }
  .card--back .brand__dot { width: 24px; height: 24px; }
  .card--back .brand__name { font-size: 17px; }

  .person { position: absolute; left: 34px; top: 94px; }
  .person__name { font-size: 15px; font-weight: 400; color: var(--ink-grey); }
  .person__first { color: var(--accent-blue); }
  .person__role { font-size: 10px; font-weight: 300; color: var(--ink-soft); margin-top: 2px; }

  .contacts {
    position: absolute; left: 34px; top: 150px;
    list-style: none; font-size: 10.5px; font-weight: 300; color: var(--ink-soft);
  }
  .contacts li { display: flex; align-items: center; gap: 8px; height: 20px; }
  .contacts svg { width: 11px; height: 11px; flex: none; }
  .contacts .address { padding-left: 0; }

  .corner-block {
    position: absolute; right: 0; bottom: 0;
    width: 150px; height: 140px;
    background: var(--brand-blue);
  }
</style>
</head>
<body>
<main class="stage">

  <section class="card card--back" aria-label="Business card, contact side">
    <div class="brand">
      <span class="brand__dot"></span>
      <span class="brand__name">Ward Compass</span>
    </div>

    <div class="person">
      <p class="person__name"><span class="person__first">Salwa</span> Kettani</p>
      <p class="person__role">CEO</p>
    </div>

    <ul class="contacts">
      <li>
        <svg viewBox="0 0 12 12" aria-hidden="true"><path fill="#2d5ea8" d="M2.5 1h2l1 2.6-1.3 1a6 6 0 0 0 3.2 3.2l1-1.3L11 7.5v2a1 1 0 0 1-1 1A9 9 0 0 1 1.5 2a1 1 0 0 1 1-1z"/></svg>
        +90 612 348 2175
      </li>
      <li>
        <svg viewBox="0 0 12 12" aria-hidden="true"><circle cx="6" cy="6" r="6" fill="#2d5ea8"/><path d="M3 4h6v4.2H3z M3 4l3 2.3L9 4" fill="none" stroke="#2a2b2d" stroke-width=".9"/></svg>
        info@wardcompass.example
      </li>
      <li>
        <svg viewBox="0 0 12 12" aria-hidden="true"><circle cx="6" cy="6" r="5.3" fill="none" stroke="#2d5ea8" stroke-width="1.2"/><ellipse cx="6" cy="6" rx="2.2" ry="5.3" fill="none" stroke="#2d5ea8" stroke-width="1"/><path d="M.8 6h10.4" stroke="#2d5ea8" stroke-width="1"/></svg>
        www.wardcompass.example
      </li>
      <li class="address">14 Annakhil 7 H.R.B. Rabat, Morocco</li>
    </ul>

    <div class="corner-block" aria-hidden="true"></div>
  </section>

  <section class="card card--front" aria-label="Business card, brand side">
    <div class="brand">
      <span class="brand__dot"></span>
      <span class="brand__name">Ward Compass</span>
    </div>
  </section>

</main>
</body>
</html>
```